Chicken Shop Menu/Flyer

Please see attached brief for flyers that i need. 3 of them are basically same design. 1 is slightly different.
I need a a5 flyer designed for take-away chicken shop. It needs to stand out and look very appealing with high quality pictures. It will have business info and specials on front page, menu on back page.
I have attached a file (wing corner flyers) with all the details you will need and some example photos but would prefer if better photos could be found from the internet. I will send more images/logos soon.
Thanks
Hi All,
I have updated the file Chicken Shop Flyers with the updated version. Sorry about the inconvenience.

```html
<!DOCTYPE html>
<html lang="en">
<head>
<meta charset="utf-8">
<title>Wing Corner &amp; Gozleme – Flyer</title>
<link rel="stylesheet" href="https://fonts.googleapis.com/css2?family=Oswald:wght@300;400;500;700&family=Lobster&family=Open+Sans:wght@700;800&display=swap">
<style>
  :root {
    --red: #ff0000;
    --blue: #1414e6;
    --white: #ffffff;
    --ink: #111111;
    --page: #f4f4f4;
    --trim: #f9c9c9;
    --food-warm: #e9b98a;
    --food-green: #9cc97a;
    --food-brown: #b86a32;
  }
  * { box-sizing: border-box; margin: 0; padding: 0; }
  html, body { width: 1200px; height: 849px; overflow: hidden; }
  body { background: var(--page); position: relative; font-family: "Oswald", sans-serif; }

  .flyer {
    position: absolute; width: 406px; height: 580px;
    background: var(--white); overflow: hidden;
    border: 1px solid #cfcfcf;
  }
  .flyer--front { left: 151px; top: 165px; }
  .flyer--back  { left: 680px; top: 167px; border-color: #222; }

  .photo { position: absolute; }
  .border-trim {
    position: absolute; left: 0; width: 100%; height: 12px;
    background: var(--trim);
  }

  /* front */
  .front__hero {
    left: 0; top: 70px; width: 406px; height: 410px;
    background:
      radial-gradient(ellipse at 30% 55%, var(--food-brown) 0%, rgba(184,106,50,.6) 25%, transparent 55%),
      radial-gradient(ellipse at 60% 75%, var(--food-green) 0%, rgba(156,201,122,.5) 30%, transparent 60%),
      radial-gradient(ellipse at 20% 25%, #f5c04a 0%, rgba(245,192,74,.4) 25%, transparent 50%),
      radial-gradient(ellipse at 85% 10%, var(--food-warm) 0%, transparent 40%);
  }
  .front__title {
    position: absolute; left: 28px; top: 18px;
    color: var(--red); font-size: 40px; font-weight: 400; line-height: 1;
    transform: scaleX(.88); transform-origin: left;
  }
  .front__subtitle {
    position: absolute; left: 36px; top: 62px;
    color: var(--blue); font-family: "Lobster", cursive; font-size: 44px; line-height: 1;
  }
  .front__inset {
    left: 209px; top: 112px; width: 180px; height: 132px;
    border: 2px solid var(--red); border-radius: 10px;
    background: linear-gradient(160deg, #d9d2c4 0%, #c79a5e 40%, #5f7f3e 60%, #e6dcc8 100%);
  }
  .front__open {
    position: absolute; left: 0; width: 100%; top: 266px; text-align: center;
    color: var(--red); font-size: 33px; font-weight: 700; letter-spacing: 1.4px; line-height: 1.1;
    -webkit-text-stroke: 1.4px var(--ink);
  }
  .front__promise {
    position: absolute; left: 0; width: 100%; top: 314px; text-align: center;
    color: var(--blue); font-family: "Open Sans", sans-serif; font-size: 28px; font-weight: 800; line-height: 1.2;
    letter-spacing: .2px;
  }
  .front__detail {
    position: absolute; left: 0; width: 100%; top: 394px; text-align: center;
    color: var(--red); font-size: 16px; font-weight: 400; line-height: 1.25;
  }
  .front__items {
    position: absolute; left: 0; width: 100%; top: 440px; text-align: center;
    color: var(--blue); font-size: 21px; font-weight: 400;
  }
  .front .border-trim { top: 478px; }
  .front__band {
    position: absolute; left: 0; top: 490px; width: 100%; height: 90px;
    background: var(--red); color: var(--white); text-align: center;
    font-family: "Open Sans", sans-serif; font-weight: 700;
  }
  .front__phone { margin-top: 8px; font-size: 14px; }
  .front__phone b { font-size: 22px; }
  .front__address { margin-top: 6px; font-size: 14px; line-height: 1.35; }

  /* back */
  .back .border-trim { top: 0; height: 16px; }
  .back__hero {
    left: 150px; top: 90px; width: 256px; height: 410px;
    background:
      radial-gradient(ellipse at 45% 40%, rgba(184,106,50,.55) 0%, transparent 45%),
      radial-gradient(ellipse at 40% 70%, rgba(156,201,122,.45) 0%, transparent 50%),
      radial-gradient(ellipse at 75% 10%, rgba(233,185,138,.5) 0%, transparent 40%);
  }
  .back__heading {
    position: absolute; left: 14px; top: 20px;
    color: var(--red); font-family: "Lobster", cursive; font-size: 46px; line-height: 1;
  }
  .menu {
    position: absolute; left: 12px; top: 84px; width: 376px;
    color: var(--blue); font-size: 13.5px; font-weight: 400; line-height: 19.6px;
  }
  .menu__row { display: flex; white-space: nowrap; align-items: baseline; }
  .menu__name { flex: 1; }
  .menu__note { font-size: 7px; }
  .menu__col1 { width: 60px; text-align: left; margin-right: 88px; }
  .menu__col2 { width: 60px; text-align: right; }
  .menu__gap { height: 19.6px; }
  .back__band {
    position: absolute; left: 0; top: 493px; width: 100%; height: 87px; background: var(--red);
  }
  .back__photo-gozleme {
    left: 14px; top: 440px; width: 136px; height: 108px; border: 2px solid var(--red); border-radius: 8px;
    background: linear-gradient(150deg, #f0e4cc 0%, #c9975a 50%, #8a5a2e 100%);
  }
  .back__photo-chicken {
    left: 165px; top: 439px; width: 96px; height: 120px; border: 2px solid var(--red); border-radius: 8px;
    background: radial-gradient(ellipse at 50% 45%, #a9462a 0%, #7a3a1e 40%, #b48a5a 75%, #6b4a2a 100%);
  }
  .partner {
    position: absolute; left: 272px; top: 434px; width: 118px; height: 118px;
    border-radius: 50%; background: var(--white); border: 3px solid var(--blue);
    display: flex; align-items: center; justify-content: center; text-align: center;
    color: var(--blue); font-size: 16px; font-weight: 500; line-height: 1.1; padding: 12px;
  }
</style>
</head>
<body>

<section class="flyer flyer--front front">
  <div class="photo front__hero" role="img" aria-label="Grilled chicken with chips, salad and bread roll"></div>
  <h1 class="front__title">Wing Corner &amp;</h1>
  <div class="front__subtitle">Gozleme</div>
  <div class="photo front__inset" role="img" aria-label="Spinach and cheese gozleme on a plate"></div>
  <p class="front__open">Now OPEN 7 days til late</p>
  <p class="front__promise">Authentic Gozleme made<br>fresh per order</p>
  <p class="front__detail">Flame Grilled Chicken, we only use the finest<br>quality chicken, marinated and grilled to perfection</p>
  <p class="front__items">Chicken Wraps &amp; Grilled Chicken Burgers</p>
  <div class="border-trim" role="img" aria-label="Ornamental scalloped border"></div>
  <div class="front__band">
    <p class="front__phone">Phone: <b>9000 4821</b></p>
    <p class="front__address">Corner of Elm Rd &amp; Market St,<br>Eastfield (Magic Hat Playhouse)</p>
  </div>
</section>

<section class="flyer flyer--back back">
  <div class="border-trim" role="img" aria-label="Ornamental scalloped border"></div>
  <div class="photo back__hero" role="img" aria-label="Faded grilled chicken and salad"></div>
  <h2 class="back__heading">Menu</h2>
  <div class="menu">
    <div class="menu__row"><span class="menu__name">Flame Grilled Chicken <span class="menu__note">(inc. garlic &amp; bread)</span></span><span style="width:130px">with reg. chips</span></div>
    <div class="menu__row"><span class="menu__name">Whole Chicken</span><span class="menu__col1">$13.50</span><span class="menu__col2">$15.50</span></div>
    <div class="menu__row"><span class="menu__name">½ Chicken</span><span class="menu__col1">$7.00</span><span class="menu__col2">$9.00</span></div>
    <div class="menu__row"><span class="menu__name">¼ Chicken</span><span class="menu__col1">$4.00</span><span class="menu__col2">$6.00</span></div>
    <div class="menu__row"><span class="menu__name">Gozleme</span></div>
    <div class="menu__row"><span class="menu__name">Spinach and cheese</span><span class="menu__col2">$7.00</span></div>
    <div class="menu__row"><span class="menu__name">Beef, spinach and cheese</span><span class="menu__col2">$8.00</span></div>
    <div class="menu__row"><span class="menu__name">Chicken, cheese and mushroom</span><span class="menu__col2">$8.00</span></div>
    <div class="menu__row"><span class="menu__name">Vegetarian <span class="menu__note">( cheese, spinach, tomato, capsicum, mushroom, onion)</span></span><span class="menu__col2">$8.00</span></div>
    <div class="menu__row"><span class="menu__name">Sucuk, Egg and Cheese</span><span class="menu__col2">$8.00</span></div>
    <div class="menu__row"><span class="menu__name">Beef and Cheese</span><span class="menu__col2">$8.00</span></div>
    <div class="menu__row"><span class="menu__name">Burgers &amp; Wraps</span></div>
    <div class="menu__row"><span class="menu__name">Chicken Wrap</span><span class="menu__col2">$7.50</span></div>
    <div class="menu__row"><span class="menu__name">Flame grilled chicken, garlic, salads wrapped in Lebanese bread</span></div>
    <div class="menu__gap"></div>
    <div class="menu__row"><span class="menu__name">Grilled Chicken Burger</span><span class="menu__col2">$7.00</span></div>
    <div class="menu__row"><span class="menu__name">Grilled chicken fillet, chilli, lettuce, tomato, cheese, mayonnaise</span></div>
  </div>
  <div class="back__band"></div>
  <div class="photo back__photo-gozleme" role="img" aria-label="Close-up of folded gozleme"></div>
  <div class="photo back__photo-chicken" role="img" aria-label="Whole roast chicken on a wooden board"></div>
  <div class="partner">Magic Hat Playhouse</div>
</section>

</body>
</html>
```